Wordpress 6 pages GLAM design for hair salon

Hi guys.
I need a glam & easy to navigate web design for my (women only) new hair salon.
I have a logo. You can see in attached files.
I like 3d backgrounds.
My favourite colours choice: any variety of pink(hot & very soft), white, black, grey.
I would like to see website very feminine, glamorous & kind of old Hollywood and Dorinda Calloway inspired.
Of course it should have plug ins, like social media, map, security etc.
My website now: http://velmoracoiffure.example

Designs what I like:
http://torvinellastudio.example
http://pelurabeautyloft.example
http://www.quillfernvisualworks.example/boutique-graphic-web-folio.html
Updates

Target Market(s)

WOMEN

Industry/Entity Type

Boutique

Requirements
Should not have
• any cartoon or other characters!

```html
<!DOCTYPE html>
<html lang="en">
<head>
<meta charset="utf-8">
<title>Velmora Hair Studio – Our Services</title>
<link href="https://fonts.googleapis.com/css2?family=Open+Sans:ital,wght@0,400;0,600;0,700;1,700&family=Squada+One&display=swap" rel="stylesheet">
<style>
:root{
  --stripe-a:#f5b6c7;
  --stripe-b:#fad1dc;
  --frame:#f7b8c9;
  --hot:#e8198b;
  --ink:#2b2b2b;
  --text:#444;
  --row-alt:#ebebeb;
  --row-hi:#ffc2ce;
  --dark:#1c1a1b;
  --bar:#f9b3c6;
}
*{box-sizing:border-box;margin:0;padding:0}
html,body{width:940px;height:1200px;overflow:hidden}
body{
  position:relative;
  font-family:"Open Sans",Arial,sans-serif;
  color:var(--text);
  background:repeating-linear-gradient(90deg,var(--stripe-a) 0 30px,var(--stripe-b) 30px 60px);
}
.abs{position:absolute}
.nav{font-family:"Squada One",Impact,sans-serif;font-size:17px;color:var(--dark);letter-spacing:.5px;top:92px}
.nav.active{border-top:1px solid var(--dark);border-bottom:1px solid var(--dark);padding:4px 6px;top:86px;margin-left:-6px}
.brand{left:387px;top:39px;width:152px;height:152px;border-radius:50%;background:var(--dark);border:6px solid var(--frame);
  display:flex;align-items:center;justify-content:center;text-align:center;color:#fff;font-family:"Squada One",Impact,sans-serif;font-size:25px;line-height:1.05;z-index:3}
.call{left:693px;top:20px;height:46px;display:flex;align-items:center;gap:6px}
.call-text{background:rgba(110,100,100,.75);color:#fff;font:700 11px/1.2 Arial,sans-serif;padding:4px 8px;margin-top:14px}
.panel{left:80px;top:123px;width:768px;height:896px;background:var(--frame);box-shadow:0 4px 10px rgba(120,60,80,.35)}
.sheet{left:86px;top:130px;width:756px;height:881px;background:#fff}
.hero{left:86px;top:130px;width:756px;height:207px;background:linear-gradient(90deg,#2a2526 0%,#4a4244 30%,#d9d3d6 55%,#3a3335 80%,#1f1b1c 100%)}
h1{left:124px;top:347px;font-size:22px;font-weight:700;color:var(--hot)}
.portrait{left:124px;top:408px;width:205px;height:206px;background:radial-gradient(circle at 50% 55%,#8c7a72,#3a302e 70%,#9aa0a6)}
.intro{left:344px;top:408px;width:455px;font-size:10px;line-height:14.4px}
.intro p{margin-bottom:15px}
.intro .motto{text-align:center;font-style:italic;font-weight:700;font-size:9.4px;text-transform:uppercase;color:var(--ink)}
.intro .gift{text-align:center}
.intro .gift b{color:var(--ink)}
h2{left:0;width:928px;text-align:center;top:621px;font-size:17px;font-weight:600;color:var(--ink)}
.prices{left:193px;top:650px;width:542px;border-collapse:collapse;border:2px solid #e2e2e2;font-size:10.5px}
.prices td{height:28.1px;padding:0 8px}
.prices td:last-child{width:110px}
.prices tr:nth-child(even) td{background:var(--row-alt)}
.prices tr.hi td{background:var(--row-hi)}
.foot h3{font-size:14.5px;font-weight:700;color:var(--ink);top:1051px}
.foot-text{font-size:10.3px;line-height:14.5px;color:#333}
.foot-links a{display:block;color:#333;font-size:10.3px;line-height:18px}
.social{top:1077px;width:40px;text-align:center;font:700 6.5px Arial,sans-serif;color:#333}
.social span{display:block;width:35px;height:35px;border-radius:50%;margin:0 auto 5px}
.bar{left:0;top:1171px;width:940px;height:29px;background:var(--bar);font-size:10px;color:#444;padding:9px 86px}
.bar a{color:var(--hot);text-decoration:none}
</style>
</head>
<body>
<nav>
  <a class="abs nav" style="left:106px">Home</a>
  <a class="abs nav" style="left:178px">About Us</a>
  <a class="abs nav active" style="left:270px">Services</a>
  <a class="abs nav" style="left:609px">Gallery</a>
  <a class="abs nav" style="left:698px">Blog</a>
  <a class="abs nav" style="left:766px">Contacts</a>
</nav>

<div class="abs call">
  <svg width="44" height="44" viewBox="0 0 44 44" aria-hidden="true"><path d="M10 12c0-4 24-4 24 0l-3 4h-4l-1-3h-8l-1 3h-4z" fill="#8a7d74"/><rect x="12" y="18" width="20" height="18" rx="4" fill="#a39488"/><circle cx="22" cy="27" r="5" fill="#e9e2dc"/></svg>
  <div class="call-text">Call us:<br>555-014-2290</div>
</div>

<div class="abs panel"></div>
<div class="abs sheet"></div>
<div class="abs hero" role="img" aria-label="Salon interior with black styling stations, mirrors and spray bottles"></div>

<div class="abs brand">VELMORA<br>Hair Studio</div>

<h1 class="abs">Our Services</h1>
<div class="abs portrait" role="img" aria-label="Portrait of a woman with voluminous dark curls"></div>
<div class="abs intro">
  <p>Continuously upgrading skills in order to perfect the latest looks by incorporating the hottest trends and styles with traditional elements, providing you a myriad of options that combine fresh, chic and classic lines.</p>
  <p class="motto">Leave my chair looking like the best version of yourself</p>
  <p>I will assist you with any questions you may have. Whether it be totally new look or just a trim – we can work together to achieve the look that suits you best.</p>
  <p class="gift"><b>Great GIFT idea!</b><br>(gift certificates are available)</p>
</div>

<h2 class="abs">Services Prices</h2>
<table class="abs prices">
  <tr><td>Woman Hair Cut (including wash, conditioning &amp; scalp massage)</td><td>from $65</td></tr>
  <tr><td>Color (exclusive luxury color line by Lumerra`s (Italy)</td><td>from $70</td></tr>
  <tr><td>Color Correction</td><td>upon consultation</td></tr>
  <tr><td>Highlights / Lowlights</td><td>$80-$180</td></tr>
  <tr><td>Straightening Hair Treatment (Formaldehyde &amp; Aldehyde FREE by Silkara)</td><td>from $325</td></tr>
  <tr><td>Hair Extensions (Fusions, Bondix)</td><td>upon consultation</td></tr>
  <tr><td>Blow Dry &amp; Styling</td><td>from $35</td></tr>
  <tr class="hi"><td>Flat Iron</td><td>$10</td></tr>
  <tr><td>Curling Iron</td><td>$20</td></tr>
  <tr><td>Updos from</td><td>$60</td></tr>
  <tr><td>Scalp &amp; Hair Treatment</td><td>from $20</td></tr>
  <tr><td>Image Consultation</td><td>free</td></tr>
</table>

<footer class="foot">
  <h3 class="abs" style="left:86px">Location</h3>
  <div class="abs foot-text" style="left:86px;top:1078px">
    <svg width="8" height="10" viewBox="0 0 8 10" aria-hidden="true"><path d="M4 0a4 4 0 0 1 4 4c0 3-4 6-4 6S0 7 0 4a4 4 0 0 1 4-4z" fill="#333"/><circle cx="4" cy="4" r="1.5" fill="#fff"/></svg>
    Velmora Hairdesign Studio<br>&nbsp;&nbsp;&nbsp;Toronto, 18 Larkspur Ave, M2K 3P8<br>
    <svg width="8" height="9" viewBox="0 0 8 9" aria-hidden="true"><path d="M1 0h2l1 2-1 1c1 2 2 3 3 3l1-1 1 2v1C4 9 0 5 1 0z" fill="#333"/></svg>
    +1 555 014 2290<br>
    <svg width="9" height="7" viewBox="0 0 9 7" aria-hidden="true"><rect x=".5" y=".5" width="8" height="6" fill="none" stroke="#333"/><path d="M.5 .5l4 3 4-3" fill="none" stroke="#333"/></svg>
    <u>hello@velmoracoiffure.example</u>
  </div>
  <h3 class="abs" style="left:313px">Hours</h3>
  <div class="abs foot-text" style="left:313px;top:1078px">
    <svg width="9" height="9" viewBox="0 0 9 9" aria-hidden="true"><circle cx="4.5" cy="4.5" r="3.8" fill="none" stroke="#333"/><path d="M4.5 2.5v2h1.5" fill="none" stroke="#333"/></svg>
    Mon - Sat: 10am - 10pm<br>&nbsp;&nbsp;&nbsp;&nbsp;Sun: 12pm - 6pm
  </div>
  <div class="abs foot-links" style="left:478px;top:1055px"><a>About us</a><a>Services</a><a>Gallery</a><a>Blog</a></div>
  <div class="abs foot-links" style="left:560px;top:1055px"><a>Blog</a><a>Testimonials</a><a>Privacy Policy</a><a>Contact Us</a></div>
  <h3 class="abs" style="left:691px">Follow us:</h3>
  <div class="abs social" style="left:688px"><span style="background:#3aa7e0"></span>CHIRRUP</div>
  <div class="abs social" style="left:735px"><span style="background:#3b5c9e"></span>FRIENDWALL</div>
  <div class="abs social" style="left:782px"><span style="background:#d9443a"></span>CIRCLEPLUS</div>
</footer>

<div class="abs bar">© 2014 Velmora Hair Studio. ALL RIGHTS RESERVED | <a>Sitemap</a></div>
</body>
</html>
```